Tolvik Commercial Cleaning is lookong for a new business card design.

A fresh new design that's professional and stylish. We need a serious upgrade to our business cards. I have included pictures of our existing ones. Our clients include professional individuals and business owners. We woupdblike something professional and upbeat. Please have fun and see what you come uo with.

Target Market(s)

Property managers, business owners, facility managers and other similar professionals

Industry/Entity Type

Janitorial

Contact Information for Business Card

Name, cell, office number, email, web address

Font styles to use
Sans Serif

Colors

Designer to choose colors to be used in the design.

Requirements
Must have
• please use the green color in our logo
Nice to have
• Bar code
Should not have
• Address

```html
<!DOCTYPE html>
<html lang="en">
<head>
<meta charset="utf-8">
<title>Tolvik Commercial Cleaning – Business Card</title>
<link rel="stylesheet" href="https://fonts.googleapis.com/css2?family=Open+Sans:wght@400;600;700;800&display=swap">
<style>
  :root {
    --stage: #333333;
    --brand-green: #3bb55a;
    --brand-green-deep: #2f8f48;
    --brand-blue: #3a68a8;
    --paper: #fbfcf3;
    --ink: #1f1f1f;
  }
  * { margin: 0; padding: 0; box-sizing: border-box; }
  html, body { width: 1200px; height: 780px; overflow: hidden; }
  body {
    background: var(--stage);
    font-family: "Open Sans", Arial, sans-serif;
    display: flex;
    align-items: center;
    justify-content: center;
    gap: 30px;
  }
  .card {
    position: relative;
    width: 560px;
    height: 320px;
    border-radius: 2px;
    overflow: hidden;
  }

  /* Back side */
  .card--back {
    background: var(--brand-green);
    display: flex;
    align-items: center;
    justify-content: center;
  }
  .card--back .brand-name {
    width: 340px;
    font-size: 44px;
    font-weight: 800;
    color: var(--brand-green-deep);
    text-align: center;
    line-height: 1.1;
  }

  /* Front side */
  .card--front { background: var(--paper); }
  .brand {
    position: absolute;
    left: 34px;
    top: 38px;
    width: 250px;
    display: flex;
    align-items: flex-start;
    gap: 12px;
  }
  .brand-mark {
    flex: none;
    width: 20px;
    height: 20px;
    margin-top: 8px;
    border-radius: 50%;
    background: var(--brand-green);
  }
  .card--front .brand-name {
    font-size: 28px;
    font-weight: 800;
    color: var(--brand-green);
    line-height: 1.12;
  }
  .accent-band {
    position: absolute;
    right: 0;
    top: 104px;
    width: 14px;
    height: 50px;
    background: var(--brand-green);
  }
  .person {
    position: absolute;
    right: 28px;
    top: 104px;
    text-align: right;
  }
  .person-name {
    font-size: 24px;
    font-weight: 800;
    line-height: 1.1;
  }
  .person-name .first { color: var(--brand-green); }
  .person-name .last { color: var(--brand-blue); }
  .person-title {
    font-size: 14px;
    font-weight: 600;
    color: var(--ink);
    margin-top: 2px;
  }
  .contact {
    position: absolute;
    left: 34px;
    bottom: 28px;
    list-style: none;
  }
  .contact-item {
    display: flex;
    align-items: center;
    gap: 10px;
    font-size: 15px;
    color: var(--ink);
    line-height: 24px;
  }
  .contact-icon { width: 14px; height: 14px; flex: none; }
</style>
</head>
<body>

  <section class="card card--back" aria-label="Business card back">
    <p class="brand-name">Tolvik Commercial Cleaning</p>
  </section>

  <section class="card card--front" aria-label="Business card front">
    <div class="brand">
      <span class="brand-mark"></span>
      <p class="brand-name">Tolvik Commercial Cleaning</p>
    </div>

    <span class="accent-band"></span>
    <div class="person">
      <p class="person-name"><span class="first">Marcus</span> <span class="last">Delaney</span></p>
      <p class="person-title">Director</p>
    </div>

    <ul class="contact">
      <li class="contact-item">
        <svg class="contact-icon" viewBox="0 0 16 16" aria-hidden="true">
          <path fill="#3bb55a" d="M3.6 1.5l2.2 2.6-1.3 1.6c.9 2 2.3 3.4 4.3 4.3l1.6-1.3 2.6 2.2-1.2 2.3C6.6 13.1 2.9 9.4 1.8 3.8z"/>
        </svg>
        (555) 010-4827
      </li>
      <li class="contact-item">
        <svg class="contact-icon" viewBox="0 0 16 16" aria-hidden="true">
          <rect x="1" y="3" width="14" height="10" rx="1" fill="#3bb55a"/>
          <path d="M1.5 3.8L8 9l6.5-5.2" fill="none" stroke="#fbfcf3" stroke-width="1.3"/>
        </svg>
        marcus@tolvikcleaning.com
      </li>
      <li class="contact-item">
        <svg class="contact-icon" viewBox="0 0 16 16" aria-hidden="true">
          <circle cx="8" cy="8" r="7" fill="#3bb55a"/>
          <path d="M1 8h14M8 1c-2.5 2.2-2.5 11.8 0 14M8 1c2.5 2.2 2.5 11.8 0 14" fill="none" stroke="#fbfcf3" stroke-width="1"/>
        </svg>
        www.tolvikcleaning.com
      </li>
    </ul>
  </section>

</body>
</html>
```